Coastline Premier Retreats Business Card Design

Design a business card for Coastline Premier Retreats. Look at the website for colors and reference. Card should have logo, name, title, office number, mobile number, email, URL and a tagline like, "Luxury Hotel & Resort Email Marketing" (This might change).

https://www.coastlinepremierretreats.example

The rest I will leave up to your imagination.

Contact Information for Business Card

Logo, name, title, office number, mobile number, email, URL and a tagline like, "Luxury Hotel & Resort Email Marketing" (This might change).

```html
<!DOCTYPE html>
<html lang="en">
<head>
<meta charset="UTF-8">
<title>Coastline Premier Retreats – Business Card</title>
<link rel="stylesheet" href="https://fonts.googleapis.com/css2?family=Montserrat:wght@400;500;700;800&display=swap">
<style>
  :root {
    --backdrop: #2b2b2b;
    --card: #1b1b1b;
    --accent: #f07a13;
    --ink: #ffffff;
    --ink-soft: #e6e6e6;
  }
  * { box-sizing: border-box; margin: 0; padding: 0; }
  html, body {
    width: 1200px; height: 900px; overflow: hidden;
    background: var(--backdrop);
    font-family: "Montserrat", Arial, sans-serif;
  }
  .sheet {
    width: 1200px; height: 900px;
    display: flex; flex-direction: column; align-items: center; justify-content: center;
    gap: 40px;
  }
  .card {
    position: relative;
    width: 700px; height: 400px;
    background: var(--card);
    border-bottom: 5px solid var(--accent);
    box-shadow: 0 14px 30px rgba(0,0,0,.55);
    overflow: hidden;
  }
  .brand {
    display: flex; align-items: center; gap: 14px;
    color: var(--ink);
    font-weight: 800;
    text-transform: uppercase;
    letter-spacing: .5px;
    line-height: 1;
  }
  .brand-square {
    width: 18px; height: 18px; background: var(--accent); flex: none;
  }

  /* Front */
  .card-front .brand {
    position: absolute; left: 0; right: 0; top: 150px;
    justify-content: center; font-size: 34px;
  }
  .tagline {
    position: absolute; left: 0; right: 0; top: 250px;
    text-align: center;
    color: var(--accent);
    font-size: 19px; font-weight: 400; letter-spacing: 1px;
  }

  /* Back */
  .card-back .brand {
    position: absolute; left: 200px; top: 70px; font-size: 28px;
  }
  .person {
    position: absolute; left: 70px; top: 236px; text-align: right; width: 270px;
  }
  .person-name {
    color: var(--accent); font-weight: 800; font-size: 30px; letter-spacing: 1.5px;
    text-transform: uppercase; line-height: 1.1;
  }
  .person-title {
    color: var(--ink); font-size: 17px; font-weight: 400; margin-top: 4px;
  }
  .divider {
    position: absolute; left: 365px; top: 180px; width: 1.5px; height: 165px;
    background: var(--accent);
  }
  .contact {
    position: absolute; left: 385px; top: 185px;
    list-style: none; color: var(--ink-soft); font-size: 14px; line-height: 1.5;
  }
  .contact-address { margin-bottom: 8px; }
  .contact-item { display: flex; align-items: center; gap: 9px; margin-bottom: 3px; }
  .contact-item svg { width: 13px; height: 13px; flex: none; fill: var(--accent); }
</style>
</head>
<body>
<main class="sheet">

  <section class="card card-front">
    <div class="brand"><span class="brand-square"></span>Coastline Premier Retreats</div>
    <p class="tagline">Luxury Hotel &amp; Resort Email Marketing</p>
  </section>

  <section class="card card-back">
    <div class="brand"><span class="brand-square"></span>Coastline Premier Retreats</div>

    <div class="person">
      <p class="person-name">Daniel Mercer</p>
      <p class="person-title">CEO/Founder</p>
    </div>

    <span class="divider"></span>

    <ul class="contact">
      <li class="contact-address">Po Box, 48 B Harbor Rd<br>North America, AB 51920</li>
      <li class="contact-item">
        <svg viewBox="0 0 16 16" aria-hidden="true"><path d="M4 0h8a1 1 0 0 1 1 1v14a1 1 0 0 1-1 1H4a1 1 0 0 1-1-1V1a1 1 0 0 1 1-1zm1 2v10h6V2zm3 11a1 1 0 1 0 0 2 1 1 0 0 0 0-2z"/></svg>
        555.214.3080
      </li>
      <li class="contact-item">
        <svg viewBox="0 0 16 16" aria-hidden="true"><path d="M3.6 1.2 5.8 3.4a1 1 0 0 1 0 1.4L4.6 6a9 9 0 0 0 5.4 5.4l1.2-1.2a1 1 0 0 1 1.4 0l2.2 2.2a1 1 0 0 1 0 1.4l-1.3 1.3c-.8.8-2.1.9-3.1.3A18 18 0 0 1 .9 5.9C.3 4.9.4 3.6 1.2 2.8L2.2 1.2a1 1 0 0 1 1.4 0z"/></svg>
        +34 600 412 275
      </li>
      <li class="contact-item">
        <svg viewBox="0 0 16 16" aria-hidden="true"><path d="M1 3h14a1 1 0 0 1 1 1v8a1 1 0 0 1-1 1H1a1 1 0 0 1-1-1V4a1 1 0 0 1 1-1zm.5 1.5v.3L8 9l6.5-4.2v-.3zm0 2V11.5h13V6.5L8 10.7z"/></svg>
        info@coastlinepremierretreats.example
      </li>
      <li class="contact-item">
        <svg viewBox="0 0 16 16" aria-hidden="true"><path d="M8 0a8 8 0 1 0 0 16A8 8 0 0 0 8 0zm5.9 7h-2.5a12 12 0 0 0-1-4.6A6 6 0 0 1 13.9 7zM8 2c.7.9 1.3 2.7 1.4 5H6.6C6.7 4.7 7.3 2.9 8 2zM5.6 2.4a12 12 0 0 0-1 4.6H2.1a6 6 0 0 1 3.5-4.6zM2.1 9h2.5a12 12 0 0 0 1 4.6A6 6 0 0 1 2.1 9zM8 14c-.7-.9-1.3-2.7-1.4-5h2.8c-.1 2.3-.7 4.1-1.4 5zm2.4-.4a12 12 0 0 0 1-4.6h2.5a6 6 0 0 1-3.5 4.6z"/></svg>
        www.coastlinepremierretreats.example
      </li>
    </ul>
  </section>

</main>
</body>
</html>
```